Vesta PR Website

Vesta PR are a PR company with a requirement for a new website. In consultation with the client, we have defined a wireframe for a homepage to show content and functionality. A PDF of the wire frame is attached.
Current site http://www.vesta-pr.co.uk/
Updates
If you are using Stock Photography - please use iStock
Dear All
Unfortunately, my client didn't like any of the designs submitted.
I've uploaded 3 examples of the type of photography that will appear in the carousel as supplied by the client.
Target Market(s)
Business to Business/Professionals - high value clients
Number of Pages Required
1 page
Requirements
Must have
- Colour scheme is attached as a .ase file from Kuler and can be viewed on Kuler if you search for 'VESTA PR Palette'
Corporate Typeface is Futura Book - use of Cufon is OK
Current Logo to be reatainedCall 2 Action Buttons will be controlled via the CMS so a generic background may be useful for these.
Nice to have
- RSS feeds

```html
<!DOCTYPE html>
<html lang="en">
<head>
<meta charset="utf-8">
<title>Vesta PR – Home</title>
<link rel="stylesheet" href="https://fonts.googleapis.com/css2?family=Jost:wght@400;500&family=Noto+Sans:wght@400;700&display=swap">
<style>
  :root {
    --teal: #4fa79c;
    --teal-light: #a8e0da;
    --teal-mid: #7ccbc2;
    --teal-dark: #3d8c84;
    --ink: #1a1a1a;
    --charcoal: #2e2e2e;
    --grey-line: #c8c8c8;
    --white: #ffffff;
    --mint-text: #cdf3ee;
  }
  * { box-sizing: border-box; margin: 0; padding: 0; }
  html, body { width: 1066px; height: 1200px; overflow: hidden; }
  body { position: relative; background: var(--white); font-family: "Noto Sans", sans-serif; color: var(--ink); }
  .abs { position: absolute; }

  /* Header */
  .site-header { left: 0; top: 0; width: 1066px; height: 119px; background: linear-gradient(#ffffff, #ececec); }
  .brand { left: 30px; top: 38px; }
  .brand-name { font-family: "Jost", sans-serif; font-weight: 400; font-size: 40px; letter-spacing: 0; color: var(--teal-dark); line-height: 1; }
  .social { right: 32px; top: 30px; display: flex; gap: 22px; font-family: "Jost", sans-serif; font-weight: 500; font-size: 19px; color: var(--teal-dark); }
  .call { right: 32px; top: 80px; font-family: "Jost", sans-serif; font-size: 26px; color: var(--ink); }

  /* Navigation */
  .main-nav { left: 0; top: 119px; width: 1066px; height: 46px; background: linear-gradient(#5a5a5a, #1e1e1e); display: flex; align-items: center; padding-left: 20px; }
  .main-nav a { font-family: "Jost", sans-serif; font-size: 18.5px; color: var(--white); text-decoration: none; padding: 0 18px; border-right: 1px solid #cfcfcf; line-height: 20px; }
  .main-nav a:last-child { border-right: none; }

  /* Hero */
  .hero { left: 20px; top: 158px; width: 1027px; height: 236px; background: var(--teal-mid); border-radius: 6px; padding: 9px; }
  .hero-inner { position: relative; width: 100%; height: 100%; border-radius: 4px; background: linear-gradient(90deg, #5fb5aa, #8fd4cb); overflow: hidden; }
  .hero-photo { position: absolute; right: 0; top: 0; width: 670px; height: 100%; background: linear-gradient(90deg, rgba(150,210,202,0) 0%, #d8e4e0 35%, #f0eeea 70%, #e7e2dc 100%); }
  .service-list { position: absolute; left: 8px; top: 6px; list-style: none; }
  .service-list li { width: 302px; height: 40.5px; background: linear-gradient(#9fd9d1, #7fc6bd); border-bottom: 1px solid #6db8ae; font-family: "Jost", sans-serif; font-size: 24px; color: var(--ink); padding: 4px 0 0 18px; }

  /* Intro */
  .intro { left: 31px; top: 422px; width: 642px; }
  .intro h1 { font-family: "Jost", sans-serif; font-weight: 400; font-size: 38px; color: var(--teal); margin-bottom: 18px; }
  .intro p { font-size: 12.6px; line-height: 16px; margin-bottom: 15px; }

  .divider { left: 691px; top: 421px; height: 483px; border-left: 2px dotted #888; }

  /* Cards */
  .card { top: 680px; width: 295px; height: 224px; border: 1px solid var(--grey-line); border-radius: 6px; background: linear-gradient(#ffffff, #dcdcdc); padding: 14px 12px; }
  .card h2 { font-family: "Jost", sans-serif; font-weight: 400; font-size: 24px; margin-bottom: 12px; }
  .card p { font-size: 12.6px; line-height: 15.5px; margin-bottom: 14px; }
  .card-client { left: 34px; }
  .card-blog { left: 365px; }
  .blog-text { width: 150px; }
  .blog-photo { left: 184px; top: 33px; width: 90px; height: 94px; background: linear-gradient(#d6d3cf, #9aa7a6); }

  /* C2A */
  .chevron { left: 862px; width: 24px; height: 34px; }
  .c2a { left: 749px; width: 249px; height: 72px; background: #1c1c1c; border-radius: 3px; padding: 5px; }
  .c2a span { display: block; height: 100%; background: linear-gradient(#4a4a4a, #2a2a2a); font-family: "Jost", sans-serif; font-size: 38px; color: var(--mint-text); text-align: center; line-height: 60px; }

  .page-frame { left: 11px; top: 394px; width: 1044px; height: 595px; border-left: 2px solid #d8d8d8; border-right: 2px solid #d8d8d8; }

  /* Footer */
  .site-footer { left: 0; top: 989px; width: 1066px; height: 164px; background: var(--teal-light); }
  .footer-links { top: 30px; list-style: none; }
  .footer-links li { font-size: 12.8px; font-weight: 700; line-height: 25.6px; }
  .links-services { left: 37px; }
  .links-social { left: 303px; }
  .signup { left: 654px; top: 12px; }
  .signup h3 { font-family: "Jost", sans-serif; font-weight: 400; font-size: 35px; margin-bottom: 6px; }
  .email-field { width: 309px; height: 42px; background: var(--white); border: 1px solid var(--ink); font-family: "Jost", sans-serif; font-size: 23px; padding: 4px 8px; margin-left: 2px; }
  .subscribe { margin-top: 10px; width: 157px; height: 38px; background: linear-gradient(#444, #0e0e0e); border: 2px solid #555; border-radius: 3px; color: var(--white); font-family: "Jost", sans-serif; font-size: 23px; text-align: center; line-height: 32px; }

  .legal-bar { left: 0; top: 1153px; width: 1066px; height: 47px; background: linear-gradient(var(--teal), #7cc8bf); }
  .legal-bar p { position: absolute; right: 22px; top: 18px; font-size: 12.8px; font-weight: 700; }
</style>
</head>
<body>
  <header class="site-header abs">
    <div class="brand abs"><span class="brand-name">Vesta PR</span></div>
    <div class="social abs"><span>Talkwave</span><span>Chirpline</span><span>Friendbook</span></div>
    <div class="call abs">Call us now 0141 555 0199</div>
  </header>

  <nav class="main-nav abs">
    <a href="#">Home</a><a href="#">Vesta Services</a><a href="#">Press Office</a><a href="#">Vesta Case Studies</a><a href="#">Vesta People</a><a href="#">Blog</a><a href="#">Vesta News</a><a href="#">Contact Us</a>
  </nav>

  <div class="page-frame abs"></div>

  <section class="hero abs">
    <div class="hero-inner">
      <div class="hero-photo" role="img" aria-label="Photo of four smiling business people in white shirts"></div>
      <ul class="service-list">
        <li>Online Public Relations</li>
        <li>Media Relations</li>
        <li>Consumer Campaigns</li>
        <li>Crisis Public Relations</li>
        <li>Internal Communications</li>
      </ul>
    </div>
  </section>

  <section class="intro abs">
    <h1>Welcome to Vesta PR</h1>
    <p>Vesta Public Relations is one of Scotland’s leading independent agencies. Founded in 2000, we were determined to create a public relations service with a real difference – hence the name.</p>
    <p>Vesta Public Relation's trademark is a fresh, creative and hard working approach to public relations. It is an approach that secures real results for our clients.</p>
    <p>We are an agency with intelligence, integrity and imagination offering a comprehensive, results driven public relations service covering traditional and online public relations strategy and support.</p>
  </section>

  <article class="card card-client abs">
    <h2>Client News</h2>
    <p>Phasellus sapien ipsum, interdum ut dapibus in, hendrerit nec nulla. Donec</p>
    <p>egestas scelerisque metus, nec placeratlectus ultrices ac. Nam sodales mollis euismod. Mauris ornare viverra dignissim.</p>
  </article>

  <article class="card card-blog abs">
    <h2>Blog Entry</h2>
    <div class="blog-photo abs" role="img" aria-label="Portrait photo of the blog author"></div>
    <p class="blog-text">Phasellus sapien ipsum, interdum ut dapibus in, hendrerit nec nulla Donec.</p>
    <p>egestas scelerisque metus, nec placeratlectus ultrices ac. Nam sodales mollis euismod. Mauris ornare viverra dignissim.</p>
  </article>

  <div class="divider abs"></div>

  <svg class="chevron abs" style="top:419px" viewBox="0 0 24 34"><path d="M2 2 L12 12 L22 2 V10 L12 20 L2 10 Z" fill="#9a9a9a"/><path d="M2 14 L12 24 L22 14 V22 L12 32 L2 22 Z" fill="#555"/></svg>
  <a class="c2a abs" style="top:454px"><span>C2A Button</span></a>
  <svg class="chevron abs" style="top:538px" viewBox="0 0 24 34"><path d="M2 2 L12 12 L22 2 V10 L12 20 L2 10 Z" fill="#9a9a9a"/><path d="M2 14 L12 24 L22 14 V22 L12 32 L2 22 Z" fill="#555"/></svg>
  <a class="c2a abs" style="top:575px"><span>C2A Button</span></a>
  <svg class="chevron abs" style="top:669px" viewBox="0 0 24 34"><path d="M2 2 L12 12 L22 2 V10 L12 20 L2 10 Z" fill="#9a9a9a"/><path d="M2 14 L12 24 L22 14 V22 L12 32 L2 22 Z" fill="#555"/></svg>
  <a class="c2a abs" style="top:706px"><span>C2A Button</span></a>
  <svg class="chevron abs" style="top:794px" viewBox="0 0 24 34"><path d="M2 2 L12 12 L22 2 V10 L12 20 L2 10 Z" fill="#9a9a9a"/><path d="M2 14 L12 24 L22 14 V22 L12 32 L2 22 Z" fill="#555"/></svg>
  <a class="c2a abs" style="top:830px"><span>C2A Button</span></a>

  <footer class="site-footer abs">
    <ul class="footer-links links-services abs">
      <li>Online Public Relations</li>
      <li>Media Relations</li>
      <li>Consumer Campaigns</li>
      <li>Crisis Public Relations</li>
      <li>Internal Communications</li>
    </ul>
    <ul class="footer-links links-social abs">
      <li>Subscribe to RSS Feed</li>
      <li>Our Friendbook page</li>
      <li>Link Three</li>
      <li>Link Four</li>
    </ul>
    <div class="signup abs">
      <h3>E-News Signup</h3>
      <div class="email-field">Email Address</div>
      <div class="subscribe">Subscribe</div>
    </div>
  </footer>

  <div class="legal-bar abs"><p>© Copyright Notice | Site Credit | Legal</p></div>
</body>
</html>
```